Business card design for Quorvel Engineering Tandem

We need a new business card design along with all the necessary to place an order. The company is Quorvel Engineering Tandem and we recently updated our logo.

```html
<!DOCTYPE html>
<html lang="en">
<head>
<meta charset="utf-8">
<title>Quorvel Engineering Tandem – Business Card</title>
<link href="https://fonts.googleapis.com/css2?family=Montserrat:wght@400;500;600&display=swap" rel="stylesheet">
<style>
  :root {
    --backdrop: #1c1b20;
    --card: #232427;
    --card-edge: #2a2b2f;
    --silver: #a5a5a6;
    --muted: #6d6e72;
    --light: #e9e9ea;
    --accent: #e3c225;
  }
  * { margin: 0; padding: 0; box-sizing: border-box; }
  html, body {
    width: 1200px; height: 801px; overflow: hidden;
    background: var(--backdrop);
    font-family: "Montserrat", sans-serif;
  }
  .stage {
    width: 1200px; height: 801px;
    display: flex; align-items: center; justify-content: center; gap: 40px;
  }
  .card {
    position: relative;
    width: 540px; height: 309px;
    background: var(--card);
    border: 1px solid var(--card-edge);
    overflow: hidden;
  }

  /* Front */
  .card--front { display: flex; flex-direction: column; align-items: center; justify-content: center; }
  .wordmark { display: flex; align-items: center; gap: 12px; }
  .wordmark__mark { width: 14px; height: 14px; background: var(--muted); }
  .wordmark__name {
    font-weight: 600; font-size: 21px; letter-spacing: 2px;
    text-transform: uppercase; color: var(--muted);
    white-space: nowrap;
  }
  .card--front .website {
    margin-top: 30px;
    font-size: 11px; letter-spacing: 4px; color: var(--light);
  }

  /* Back */
  .card--back .wordmark {
    position: absolute; top: 86px; left: 0; right: 0; justify-content: center;
  }
  .card--back .wordmark__mark { background: var(--accent); }
  .card--back .wordmark__name { color: var(--silver); }
  .holder { position: absolute; left: 34px; top: 190px; }
  .holder__name {
    font-weight: 600; font-size: 15px; letter-spacing: 0.5px;
    text-transform: uppercase; color: var(--light);
  }
  .holder__role { font-size: 12px; color: var(--accent); margin-top: 2px; }
  .rule {
    position: absolute; left: 34px; right: 34px; top: 236px;
    height: 1px; background: var(--accent);
  }
  .contacts {
    position: absolute; left: 34px; right: 34px; top: 248px;
    display: flex; align-items: center; justify-content: space-between;
    font-size: 11px; color: var(--light); white-space: nowrap;
  }
  .contact { display: flex; align-items: center; gap: 7px; }
  .contact svg { width: 12px; height: 12px; flex: none; }
  .divider { width: 1px; height: 12px; background: var(--light); opacity: .7; }
  .band {
    position: absolute; left: 0; right: 0; bottom: 0;
    height: 8px; background: var(--accent);
  }
</style>
</head>
<body>
<main class="stage">
  <section class="card card--front" aria-label="Card front">
    <div class="wordmark">
      <span class="wordmark__mark"></span>
      <span class="wordmark__name">Quorvel Engineering Tandem</span>
    </div>
    <p class="website">www.quorveltandem.co</p>
  </section>

  <section class="card card--back" aria-label="Card back">
    <div class="wordmark">
      <span class="wordmark__mark"></span>
      <span class="wordmark__name">Quorvel Engineering Tandem</span>
    </div>

    <div class="holder">
      <p class="holder__name">Daren K. Voss</p>
      <p class="holder__role">Partner</p>
    </div>
    <div class="rule"></div>

    <div class="contacts">
      <span class="contact">
        <svg viewBox="0 0 12 12" aria-hidden="true"><rect x="2.5" y="0.8" width="7" height="10.4" rx="1.2" fill="none" stroke="var(--accent)" stroke-width="1.4"/><circle cx="6" cy="9.2" r="0.7" fill="var(--accent)"/></svg>
        0198 765 432
      </span>
      <span class="divider"></span>
      <span class="contact">
        <svg viewBox="0 0 12 12" aria-hidden="true"><rect x="0.7" y="2.2" width="10.6" height="7.6" fill="var(--accent)"/><path d="M0.7 2.2 6 6.6 11.3 2.2" fill="none" stroke="var(--card)" stroke-width="1"/></svg>
        info@quorveltandem.co
      </span>
      <span class="divider"></span>
      <span class="contact">
        <svg viewBox="0 0 12 12" aria-hidden="true"><circle cx="6" cy="6" r="5" fill="none" stroke="var(--accent)" stroke-width="1.2"/><ellipse cx="6" cy="6" rx="2.2" ry="5" fill="none" stroke="var(--accent)" stroke-width="1"/><path d="M1 6h10" stroke="var(--accent)" stroke-width="1"/></svg>
        www.quorveltandem.co
      </span>
    </div>
    <div class="band"></div>
  </section>
</main>
</body>
</html>
```